Redesign Local Plumber Website

redesign of existing plumbing website

Mobile Responsive
Professional
modern
easy enquiry
Map embed

Please see existing site for text and images. Please feel free to suggest improvements and any additional features
callthepipeteam.com.au

attached is logo and the Australian owned badge which we also want featuring

Target Market(s)

Plumbing & Gas Services

Industry/Entity Type

Plumbing

Font styles to use
Sans Serif

Requirements
Must have
• existing logo
Nice to have
• new design
Should not have
• same design

```html
<!DOCTYPE html>
<html lang="en">
<head>
<meta charset="utf-8">
<title>Call The Pipe Team – Plumbing &amp; Gas Services</title>
<link href="https://fonts.googleapis.com/css2?family=Roboto:wght@300;400;500;700;900&display=swap" rel="stylesheet">
<style>
:root{
  --blue:#1c9ad6;
  --blue-dark:#0d6fb0;
  --ink:#1f1f1f;
  --text:#6b6b6b;
  --partner:#5a5a5a;
  --partner-mark:#c9c9c9;
  --maroon:#8e1b17;
  --footer:#1e1e1e;
  --footer-bar:#141414;
  --line:#e6e6e6;
  --white:#fff;
}
*{margin:0;padding:0;box-sizing:border-box}
html,body{width:1200px;height:5025px;overflow:hidden}
body{font-family:'Roboto',sans-serif;color:var(--ink);background:var(--white);position:relative}
.abs{position:absolute}
/* header */
.site-header{position:absolute;top:0;left:0;width:1200px;height:98px;border-top:3px solid var(--blue);border-bottom:1px solid var(--line)}
.brand{position:absolute;left:96px;top:30px;display:flex;align-items:center;gap:10px;font-weight:900;font-size:22px;color:var(--blue-dark);text-transform:uppercase;letter-spacing:.5px}
.brand-dot{width:30px;height:30px;border-radius:50%;background:var(--blue-dark)}
.call{position:absolute;left:648px;top:32px;display:flex;align-items:center;gap:12px;font-size:15px;color:var(--ink)}
.call strong{color:var(--blue);font-size:21px;font-weight:500}
.call-icon{width:32px;height:32px;border:2px solid var(--blue);border-radius:50%;display:flex;align-items:center;justify-content:center}
.btn-quote{position:absolute;left:952px;top:26px;width:135px;height:45px;background:var(--blue);color:#fff;font-size:13px;font-weight:700;border-radius:4px;display:flex;align-items:center;justify-content:center}
.main-nav{position:absolute;top:98px;left:0;width:1200px;height:62px;display:flex;align-items:center;font-size:13px;font-weight:500}
.main-nav span{position:absolute}
.main-nav .active{color:var(--blue)}
/* hero */
.hero{position:absolute;top:160px;left:0;width:1200px;height:515px;background:linear-gradient(100deg,#9aa4ab 0%,#6d7a85 45%,#41556f 75%,#2e3f57 100%)}
.hero-copy{position:absolute;left:112px;top:130px;border-left:3px solid #fff;padding-left:14px;color:#fff}
.hero-copy h1{font-size:42px;font-weight:900;line-height:44px}
.hero-copy p{font-size:13px;line-height:25px;margin-top:8px;width:390px}
.btn-start{display:inline-flex;margin-top:14px;background:var(--blue);padding:14px 22px;font-size:13px;font-weight:700;border-radius:4px}
.dots{position:absolute;left:108px;top:452px;display:flex;gap:5px}
.dots i{width:11px;height:11px;border:2px solid #fff;border-radius:50%}
.dots i:first-child{background:#fff}
/* partners */
.eyebrow{font-size:12px;color:var(--text);text-transform:uppercase;letter-spacing:.5px}
.partners-label{position:absolute;top:733px;width:1200px;text-align:center}
.partner{position:absolute;top:770px;height:46px;display:flex;align-items:center;gap:8px;font-size:19px;font-weight:700;color:var(--partner)}
.partner i{width:22px;height:22px;border-radius:50%;background:var(--partner-mark)}
.partner-badge{position:absolute;left:837px;top:770px;width:166px;height:48px;background:#d9dde0}
/* about */
.about{position:absolute;left:110px;top:892px;width:470px}
.about h2{font-size:34px;font-weight:900;margin:8px 0 22px}
.about p{font-size:13px;line-height:25.5px;color:var(--text);text-align:justify;margin-bottom:24px}
.btn-maroon{display:inline-flex;background:var(--maroon);color:#fff;font-size:13px;font-weight:700;padding:16px 23px;border-radius:5px}
.about-photo{position:absolute;top:893px;height:374px}
.badge{position:absolute;left:788px;top:1005px;width:150px;height:150px;border-radius:50%;background:#23813f;border:8px solid #fff}
/* products */
.section-title{position:absolute;width:1200px;text-align:center;font-size:32px;font-weight:700}
.tile{position:absolute;width:384px;height:238px;display:flex;flex-direction:column;align-items:center;justify-content:center;color:#fff;font-size:24px;font-weight:700;text-align:center;line-height:26px}
.tile::after{content:"";width:42px;height:3px;background:#fff;margin-top:12px}
/* services */
.services{position:absolute;top:2023px;left:0;width:1200px;height:888px;background:linear-gradient(180deg,#1ba0e0 0%,#2b94d2 55%,#1ba0e0 100%)}
.services .eyebrow{position:absolute;top:92px;width:1200px;text-align:center;color:#fff;font-weight:700;font-size:11px}
.services h2{position:absolute;top:118px;width:1200px;text-align:center;color:#fff;font-size:34px;font-weight:700}
.svc{position:absolute;height:277px;color:#fff}
.svc-img{position:absolute;inset:0}
.svc-body{position:absolute;left:28px;top:22px;width:215px}
.svc-body h3{font-size:21px;font-weight:700;margin-bottom:18px}
.svc-body li{list-style:none;font-size:12.5px;line-height:25px;padding-left:16px;position:relative}
.svc-body li::before{content:"»";position:absolute;left:0}
.svc-body li.gap{margin-top:25px}
.svc-body .more{display:block;font-size:13px;font-weight:700;margin-top:8px;padding-left:3px}
/* showroom */
.shot{position:absolute}
.wise-title{position:absolute;top:3625px;width:1200px;text-align:center;font-size:20px;font-weight:700}
.cert{position:absolute;top:3697px;width:122px;height:126px;background:#d9dde0}
/* quick response */
.quick{position:absolute;top:3930px;left:0;width:1200px;height:378px;background:linear-gradient(90deg,#1f8fcf 0%,#2a9ee0 55%,#1c8ccc 100%)}
.quick-copy{position:absolute;left:110px;top:84px;color:#fff}
.quick-copy h3{font-size:22px;font-weight:700;margin-bottom:12px}
.quick-copy p{font-size:13px;line-height:26px;width:470px}
.quick-phone{display:flex;align-items:center;gap:16px;font-size:31px;font-weight:700;margin:16px 0 20px}
.ghost{display:inline-flex;border:2px solid #fff;border-radius:6px;padding:16px 20px;font-size:13px;font-weight:500;margin-right:12px}
.man{position:absolute;left:760px;top:3834px;width:390px;height:474px}
/* map + form */
.map{position:absolute;top:4308px;left:0;width:1200px;height:332px;background:linear-gradient(135deg,#e4ece2 0%,#eef0ea 40%,#dfe8df 100%)}
.direction{position:absolute;left:38px;top:20px;background:#fff;padding:14px 20px;font-size:13px;font-weight:500;box-shadow:0 1px 4px rgba(0,0,0,.2)}
.form-card{position:absolute;z-index:5;left:681px;top:4441px;width:406px;height:410px;background:#fff;box-shadow:0 2px 10px rgba(0,0,0,.12);padding:0 40px}
.field{border-bottom:1px solid var(--line);font-size:13px;color:#8a8a8a;padding:16px 2px 10px}
.field.msg{padding-top:86px}
.btn-contact{margin-top:36px;height:56px;background:var(--maroon);color:#fff;border-radius:6px;display:flex;align-items:center;justify-content:center;font-size:13px;font-weight:700}
/* footer */
.site-footer{position:absolute;top:4640px;left:0;width:1200px;height:296px;background:var(--footer);color:#fff}
.foot-col{position:absolute;top:70px}
.foot-col h4{font-size:20px;font-weight:700;margin-bottom:14px}
.foot-col li{list-style:none;font-size:13px;line-height:25.5px}
.contact-row{display:flex;gap:22px;font-size:13px;line-height:25px;margin-bottom:18px}
.contact-row svg{flex:none;margin-top:6px}
.foot-bar{position:absolute;top:4936px;left:0;width:1200px;height:89px;background:var(--footer-bar);color:#fff}
.cards{position:absolute;left:114px;top:34px;display:flex;gap:4px}
.cards i{width:33px;height:22px;background:#5a5f66;border-radius:2px}
.copyright{position:absolute;left:660px;top:38px;font-size:13px}
</style>
</head>
<body>

<header class="site-header">
  <div class="brand"><span class="brand-dot"></span>Call The Pipe Team</div>
  <div class="call">
    <span class="call-icon"><svg width="16" height="16" viewBox="0 0 24 24"><path fill="#1c9ad6" d="M6.6 10.8a15.1 15.1 0 0 0 6.6 6.6l2.2-2.2a1 1 0 0 1 1-.25 11.4 11.4 0 0 0 3.6.57 1 1 0 0 1 1 1V20a1 1 0 0 1-1 1A17 17 0 0 1 3 4a1 1 0 0 1 1-1h3.5a1 1 0 0 1 1 1c0 1.25.2 2.45.57 3.57a1 1 0 0 1-.25 1z"/></svg></span>
    <span>Call us Today : <strong>1800 555 019</strong></span>
  </div>
  <div class="btn-quote">GET A QUOTE</div>
</header>

<nav class="main-nav">
  <span class="active" style="left:124px">HOME</span>
  <span style="left:273px">ABOUT US</span>
  <span style="left:451px">SERVICES</span>
  <span style="left:627px">SEPTICS</span>
  <span style="left:794px">PRODUCTS</span>
  <span style="left:977px">CONTACT US</span>
</nav>

<section class="hero" role="img" aria-label="Plumber holding a tablet beside a tool bag and kitchen sink">
  <div class="hero-copy">
    <h1>PLUMBING &amp; GAS<br>SERVICES</h1>
    <p>Call The Pipe Team is a family run business based in Ridgeford since 2004</p>
    <span class="btn-start">GET STARTED</span>
  </div>
  <div class="dots"><i></i><i></i><i></i><i></i></div>
</section>

<p class="eyebrow partners-label">We are proud member of</p>
<div class="partner" style="left:214px"><i></i>Ambrolux</div>
<div class="partner" style="left:426px"><i></i>Kelvara</div>
<div class="partner" style="left:636px"><i></i>Tarnby Pumps</div>
<div class="partner-badge" role="img" aria-label="Partner membership badge"></div>

<section class="about">
  <p class="eyebrow" style="margin:0">About us</p>
  <h2>CALL THE PIPE TEAM</h2>
  <p>Daniel has been in the plumbing and gas industry since high school, his father Ray is a plumber and estimator. Daniel has trained with reputable plumbers of his time and achieved apprentice of the year 2 years running, then taking out the "Apprentice of the Year" award for all trades during his apprenticeship.</p>
  <p>A member of Master Trades Guild master-plumbing and an Eco Coast member, Daniel maintains a high level of education and frequently refreshes his knowledge with current trends and regulations.</p>
  <span class="btn-maroon">LEARN MORE</span>
</section>
<div class="about-photo" style="left:614px;width:243px;background:linear-gradient(160deg,#cfd3d6,#8e969c)" role="img" aria-label="Plumber fixing pipes under a sink"></div>
<div class="about-photo" style="left:871px;width:243px;background:linear-gradient(160deg,#7a5d4a,#3f4b66)" role="img" aria-label="Plumber with hoses and tool belt"></div>
<div class="badge" role="img" aria-label="Australian owned badge"></div>

<h2 class="section-title" style="top:1360px">OUR PRODUCTS &amp; SERVICES</h2>
<div class="tile" style="left:10px;top:1432px;background:linear-gradient(135deg,#8f9599,#4f5559)" role="img" aria-label="Showroom tapware">Showroom</div>
<div class="tile" style="left:408px;top:1432px;background:linear-gradient(135deg,#5c4b3f,#2f3a4c)" role="img" aria-label="Installing treatment units">Supply and install ATUs</div>
<div class="tile" style="left:805px;top:1432px;background:linear-gradient(135deg,#4f6478,#263447)" role="img" aria-label="Plumber reviewing plans">New Housing and<br>Renovations</div>
<div class="tile" style="left:10px;top:1682px;background:linear-gradient(135deg,#766a63,#3b3a3e)" role="img" aria-label="Hot water pipework">Hot Water Units</div>
<div class="tile" style="left:408px;top:1682px;background:linear-gradient(135deg,#4a3c35,#1f1f22)" role="img" aria-label="Gas fitting with wrench">Gas installations</div>
<div class="tile" style="left:805px;top:1682px;background:linear-gradient(135deg,#8c9398,#4a5056)" role="img" aria-label="Pressure vessels and pumps">Pumps, Pressure vessels<br>and parts.</div>

<section class="services">
  <p class="eyebrow">What we do</p>
  <h2>OUR SERVICES</h2>
</section>
<div class="svc" style="left:111px;top:2211px;width:472px">
  <div class="svc-img" style="background:linear-gradient(90deg,#1d2430 0%,#26364c 45%,#2f66a8 100%)" role="img" aria-label="Plumber working on pipes"></div>
  <div class="svc-body">
    <h3>PLUMBING</h3>
    <ul><li>Taps</li><li>Sinks – Kitchen Bathroom and Laundry, BBQ areas</li><li>Toilets</li><li>Baths</li><li>Showers</li></ul>
    <span class="more">LEARN MORE</span>
  </div>
</div>
<div class="svc" style="left:617px;top:2211px;width:472px">
  <div class="svc-img" style="background:linear-gradient(90deg,#1f252d 0%,#3a4552 55%,#8b9aa8 100%)" role="img" aria-label="Gas fitter at work"></div>
  <div class="svc-body">
    <h3>GAS SERVICES</h3>
    <ul><li>All gas pipework installations to kitchen, heaters, BBQ's and Hot water Units</li><li class="gap">Supply and install gas Hot Water Units</li></ul>
    <span class="more">LEARN MORE</span>
  </div>
</div>
<div class="svc" style="left:111px;top:2527px;width:978px">
  <div class="svc-img" style="background:linear-gradient(90deg,#1e2329 0%,#3d464f 25%,#9aa3aa 60%,#c9d0d5 100%)" role="img" aria-label="Industrial pump room installation"></div>
  <div class="svc-body">
    <h3>INSTALLATIONS</h3>
    <ul><li>All Plumbing and Gas installations – Domestic and Commercial</li><li class="gap">Renovations and New Housing</li></ul>
    <span class="more">LEARN MORE</span>
  </div>
</div>

<h2 class="section-title" style="top:3006px">VIEW OUR SHOWROOM</h2>
<div class="shot" style="left:111px;top:3073px;width:478px;height:219px;background:linear-gradient(135deg,#dfe3e6,#9fa8ae)" role="img" aria-label="Row of chrome basin taps"></div>
<div class="shot" style="left:609px;top:3073px;width:228px;height:219px;background:linear-gradient(160deg,#c9b9a6,#7d6a58)" role="img" aria-label="White toilet suite"></div>
<div class="shot" style="left:857px;top:3073px;width:230px;height:219px;background:linear-gradient(135deg,#e3e3e3,#8c8c8c)" role="img" aria-label="Chrome pipe fittings"></div>
<div class="shot" style="left:111px;top:3307px;width:230px;height:219px;background:linear-gradient(135deg,#eceeef,#a9b0b5)" role="img" aria-label="Hand turning a tap"></div>
<div class="shot" style="left:359px;top:3307px;width:230px;height:219px;background:linear-gradient(180deg,#9fc1e6,#e9ecef 50%,#4a4a4a)" role="img" aria-label="Bathroom vanity units"></div>
<div class="shot" style="left:609px;top:3307px;width:478px;height:219px;background:linear-gradient(135deg,#8d9194,#d8d6d0 60%,#a89a83)" role="img" aria-label="Rain shower head"></div>

<h3 class="wise-title">We are Water Wise Experts and Master Trades</h3>
<div class="cert" style="left:343px;border-radius:8px" role="img" aria-label="Water Smart specialist certificate"></div>
<div class="cert" style="left:526px;border-radius:50%" role="img" aria-label="Master Trades Guild certificate"></div>
<div class="cert" style="left:709px;border-radius:50%" role="img" aria-label="Eco Coast certificate"></div>

<section class="quick">
  <div class="quick-copy">
    <h3>QUICK RESPONSE</h3>
    <p>If you've had enough of tradespeople who never turn up when they say they will, call Daniel at Call The Pipe Team.</p>
    <div class="quick-phone"><svg width="24" height="24" viewBox="0 0 24 24"><path fill="#fff" d="M6.6 10.8a15.1 15.1 0 0 0 6.6 6.6l2.2-2.2a1 1 0 0 1 1-.25 11.4 11.4 0 0 0 3.6.57 1 1 0 0 1 1 1V20a1 1 0 0 1-1 1A17 17 0 0 1 3 4a1 1 0 0 1 1-1h3.5a1 1 0 0 1 1 1c0 1.25.2 2.45.57 3.57a1 1 0 0 1-.25 1z"/></svg>+1800 555 019</div>
    <span class="ghost">Schedule a Services call</span><span class="ghost">View all Services</span>
  </div>
</section>
<div class="man" style="background:linear-gradient(180deg,rgba(31,58,107,0) 0%,#233a6b 30%,#1e2f55 100%)" role="img" aria-label="Plumber holding a pipe wrench"></div>

<section class="map" role="img" aria-label="Map showing the business location">
  <div class="direction">GET DIRECTION</div>
  <svg class="abs" style="left:562px;top:100px" width="26" height="36" viewBox="0 0 24 34"><path fill="#d93025" d="M12 0a12 12 0 0 0-12 12c0 9 12 22 12 22s12-13 12-22A12 12 0 0 0 12 0z"/><circle cx="12" cy="12" r="4.5" fill="#8e1410"/></svg>
</section>

<footer class="site-footer">
  <div class="foot-col" style="left:110px">
    <h4>Quick Links</h4>
    <ul><li>Home</li><li>About Us</li><li>Services</li><li>Septics</li><li>Products</li><li>Contact Us</li></ul>
  </div>
  <div class="foot-col" style="left:316px">
    <h4>Contact us</h4>
    <div class="contact-row"><svg width="10" height="14" viewBox="0 0 24 34"><path fill="#fff" d="M12 0a12 12 0 0 0-12 12c0 9 12 22 12 22s12-13 12-22A12 12 0 0 0 12 0z"/></svg><span>27 Kestrel Road, Ridgeford<br>WA 6590</span></div>
    <div class="contact-row"><svg width="12" height="10" viewBox="0 0 24 18"><path fill="#fff" d="M0 0h24v18H0z"/><path fill="none" stroke="#1e1e1e" stroke-width="2" d="M0 1l12 9 12-9"/></svg><span>office@callthepipeteam.com.au</span></div>
    <div class="contact-row"><svg width="12" height="12" viewBox="0 0 24 24"><path fill="#fff" d="M6.6 10.8a15.1 15.1 0 0 0 6.6 6.6l2.2-2.2a1 1 0 0 1 1-.25 11.4 11.4 0 0 0 3.6.57 1 1 0 0 1 1 1V20a1 1 0 0 1-1 1A17 17 0 0 1 3 4a1 1 0 0 1 1-1h3.5a1 1 0 0 1 1 1c0 1.25.2 2.45.57 3.57a1 1 0 0 1-.25 1z"/></svg><span>+1800 555 019</span></div>
  </div>
</footer>

<form class="form-card">
  <div class="field" style="margin-top:12px">Name</div>
  <div class="field">Email address</div>
  <div class="field">Phone</div>
  <div class="field msg">Message</div>
  <div class="btn-contact">CONTACT NOW</div>
</form>

<div class="foot-bar">
  <div class="cards"><i></i><i></i><i></i><i></i><i></i><i></i></div>
  <p class="copyright">© Copyrights 2020 Call The Pipe Team. All Rights Reserved.</p>
</div>

</body>
</html>
```